automotive repair and collision repair shop card

our company is called K.L Motor service we are a automotive repair company
we also do government inspections. the company information is on the cards. I would like you to use my new logo and create a new card and use the information from my old card. Good Luck!!

Industry/Entity Type

Car Repair

Contact Information for Business Card

Address: #417-18842 52 Ave, Surrey, BC V5K 8R3
Phone:(604) 555-0187
fax 604 555 0193
website www.klmotorworks.example

Font styles to use
Serif
Sans Serif

Requirements
Must have
• all the information
Should not have
• the owner and there name

```html
<!DOCTYPE html>
<html lang="en">
<head>
<meta charset="utf-8">
<title>K.L Motor Service – Business Card</title>
<link rel="stylesheet" href="https://fonts.googleapis.com/css2?family=Oswald:wght@300;400&family=Roboto+Condensed:wght@300&family=Source+Sans+3:wght@400&display=swap">
<style>
  :root {
    --backdrop: #e6e6e8;
    --card: #a4a5a9;
    --wheel: #97989c;
    --art: #3a3b3e;
    --ink-light: #ffffff;
    --ink-dark: #1f1f21;
    --rule: #2a2a2c;
  }
  * { margin: 0; padding: 0; box-sizing: border-box; }
  html, body { width: 1200px; height: 750px; overflow: hidden; }
  body { background: var(--backdrop); position: relative; }

  .card {
    position: absolute;
    top: 201px;
    width: 559px;
    height: 319px;
    background: var(--card);
    overflow: hidden;
  }
  .card--front { left: 28px; }
  .card--back { left: 614px; width: 558px; }

  .wheel-decor {
    position: absolute;
    width: 360px;
    height: 360px;
    border-radius: 50%;
    background: var(--wheel);
  }
  .card--front .wheel-decor { left: 390px; top: 21px; }
  .card--back .wheel-decor { left: -196px; top: 21px; }

  .car-art {
    position: absolute;
    background: linear-gradient(180deg, #55565a 0%, var(--art) 100%);
    border-radius: 40px 60px 14px 14px;
  }
  .card--front .car-art { left: 30px; top: 46px; width: 352px; height: 92px; }
  .card--back .car-art { left: 176px; top: 80px; width: 340px; height: 90px; }

  .brand {
    position: absolute;
    text-align: right;
    color: var(--ink-light);
  }
  .brand__name {
    font-family: "Oswald", sans-serif;
    font-weight: 300;
    font-size: 42px;
    line-height: 1;
    letter-spacing: 0.5px;
    white-space: nowrap;
  }
  .brand__tagline {
    font-family: "Roboto Condensed", sans-serif;
    font-weight: 300;
    font-size: 15px;
    line-height: 1;
    margin-top: 3px;
  }
  .card--front .brand { right: 171px; top: 139px; }
  .card--back .brand { right: 29px; top: 177px; }

  .contact-rule {
    position: absolute;
    left: 20px;
    top: 230px;
    width: 372px;
    height: 2px;
    background: var(--rule);
  }
  .contact {
    position: absolute;
    display: flex;
    align-items: center;
    gap: 9px;
    font-family: "Source Sans 3", sans-serif;
    font-size: 13px;
    color: var(--ink-light);
    white-space: nowrap;
  }
  .contact svg { width: 16px; height: 16px; flex: none; }
  .contact--email { left: 21px; top: 232px; }
  .contact--web { left: 21px; top: 255px; }
  .contact--fax { left: 276px; top: 232px; }
  .contact--phone { left: 276px; top: 255px; }
  .contact { height: 22px; }

  .address {
    position: absolute;
    right: 29px;
    top: 272px;
    font-family: "Source Sans 3", sans-serif;
    font-size: 12px;
    color: var(--ink-light);
    white-space: nowrap;
  }
</style>
</head>
<body>

  <section class="card card--front">
    <div class="wheel-decor" role="img" aria-label="Faint alloy wheel decoration"></div>
    <div class="car-art" role="img" aria-label="Sports car illustration in dark grey"></div>

    <div class="brand">
      <div class="brand__name">K.L MOTOR SERVICE</div>
      <div class="brand__tagline">One Stop Repair Shop</div>
    </div>

    <div class="contact-rule"></div>

    <div class="contact contact--email">
      <svg viewBox="0 0 16 16" aria-hidden="true"><rect x="1.5" y="3.5" width="13" height="9" fill="none" stroke="#1f1f21" stroke-width="1.4"/><path d="M1.5 3.5 8 9l6.5-5.5" fill="none" stroke="#1f1f21" stroke-width="1.4"/></svg>
      <span>info@klmotorworks.example</span>
    </div>
    <div class="contact contact--web">
      <svg viewBox="0 0 16 16" aria-hidden="true"><circle cx="8" cy="8" r="6.3" fill="none" stroke="#1f1f21" stroke-width="1.3"/><ellipse cx="8" cy="8" rx="2.8" ry="6.3" fill="none" stroke="#1f1f21" stroke-width="1.1"/><path d="M1.7 8h12.6M2.8 4.8h10.4M2.8 11.2h10.4" stroke="#1f1f21" stroke-width="1.1"/></svg>
      <span>www.klmotorworks.example</span>
    </div>
    <div class="contact contact--fax">
      <svg viewBox="0 0 16 16" aria-hidden="true"><rect x="4" y="2" width="8" height="4" fill="#1f1f21"/><rect x="1.5" y="6" width="13" height="6" rx="1" fill="#1f1f21"/><rect x="4" y="10" width="8" height="4" fill="#1f1f21" stroke="#a4a5a9" stroke-width="0.8"/></svg>
      <span>604 555 0193</span>
    </div>
    <div class="contact contact--phone">
      <svg viewBox="0 0 16 16" aria-hidden="true"><path d="M4.2 1.8 6.3 4.6 5 6.2c.8 1.8 2 3.1 3.8 4l1.5-1.3 2.9 2-1 2.3c-.4.8-1.3 1-2.1.7C6.4 12.6 3.5 9.7 2.3 5.9c-.3-.9 0-1.8.7-2.3z" fill="#1f1f21"/></svg>
      <span>(604) 555-0187</span>
    </div>
  </section>

  <section class="card card--back">
    <div class="wheel-decor" role="img" aria-label="Faint alloy wheel decoration"></div>
    <div class="car-art" role="img" aria-label="Sports car illustration in dark grey"></div>

    <div class="brand">
      <div class="brand__name">K.L MOTOR SERVICE</div>
      <div class="brand__tagline">One Stop Repair Shop</div>
    </div>

    <div class="address">#417-18842 52 Ave, Surrey, BC V5K 8R3</div>
  </section>

</body>
</html>
```